Business Card and Letterhead for Pimlu - modern real estate business

I need a double sided business card design for Pimlu. Please see business card brief here https://files.trelvonadocs.com/sheet/r/7QzTmWbaXLJnoPEd-kRyUgFhHsstbvCe2qfoMxDa_pz/view?mode=shared

Please feel free to design the business cards however you feel best. I am happy to give some creative freedoms and then provide feedback from there.

Please then also create a letterhead to match the business card design

Colors

Designer to choose colors to be used in the design.

Requirements
Must have
• Must be a modern, elegant business card which looks very professional

```html
<!DOCTYPE html>
<html lang="en">
<head>
<meta charset="UTF-8">
<title>Pimlu Business Card</title>
<link href="https://fonts.googleapis.com/css2?family=Montserrat:wght@400;500;600;700&display=swap" rel="stylesheet">
<style>
  :root {
    --brand-red: #e01f26;
    --card-black: #1e1e1e;
    --paper-white: #ffffff;
    --canvas-grey: #d9dadc;
    --photo-dark: #3a3b3f;
    --photo-light: #e9e6e2;
  }
  * { box-sizing: border-box; margin: 0; padding: 0; }
  html, body {
    width: 1200px; height: 800px; overflow: hidden;
    background: var(--canvas-grey);
    font-family: "Montserrat", sans-serif;
  }
  .stage {
    width: 1200px; height: 800px;
    display: flex; align-items: center; justify-content: center; gap: 40px;
  }
  .card {
    position: relative; width: 540px; height: 310px; overflow: hidden;
    box-shadow: 0 6px 18px rgba(0,0,0,0.18);
  }
  /* Back side */
  .card-back {
    background: var(--card-black);
    display: flex; align-items: center; justify-content: center;
  }
  .card-back .wordmark {
    color: var(--brand-red); font-weight: 600; font-size: 78px; letter-spacing: 4px;
  }
  /* Front side */
  .card-front { background: var(--paper-white); }
  .front-wordmark {
    position: absolute; left: 34px; top: 34px;
    color: var(--brand-red); font-weight: 600; font-size: 44px; letter-spacing: 2px;
  }
  .red-band {
    position: absolute; left: 0; right: 0; top: 124px; height: 50px;
    background: var(--brand-red);
  }
  .dark-base {
    position: absolute; left: 0; right: 0; top: 174px; bottom: 0;
    background: var(--card-black);
  }
  .agent-name {
    position: absolute; left: 60px; top: 131px;
    color: var(--paper-white); font-weight: 700; font-size: 15px; letter-spacing: 0.5px;
  }
  .agent-title {
    position: absolute; left: 60px; top: 151px;
    color: var(--paper-white); font-weight: 400; font-size: 13px;
  }
  .contact {
    position: absolute; left: 40px; top: 188px;
    color: var(--paper-white); font-size: 13px; line-height: 19px;
  }
  .contact .address { padding-left: 14px; margin-bottom: 2px; }
  .contact-row { display: flex; align-items: center; gap: 6px; }
  .contact-row svg { width: 10px; height: 10px; flex: none; }
  .agent-photo {
    position: absolute; right: 34px; top: 72px; width: 230px; bottom: 0;
    background: linear-gradient(180deg, var(--photo-light) 0%, #c9b3a4 30%, var(--photo-dark) 48%, #2a2a2d 100%);
  }
</style>
</head>
<body>
<main class="stage">
  <section class="card card-back" aria-label="Business card back">
    <span class="wordmark">PIMLU</span>
  </section>

  <section class="card card-front" aria-label="Business card front">
    <span class="front-wordmark">PIMLU</span>
    <div class="red-band"></div>
    <div class="dark-base"></div>
    <div class="agent-photo" role="img" aria-label="Portrait photo of the agent in a dark suit"></div>
    <span class="agent-name">LIAM CARVER</span>
    <span class="agent-title">Licenced Real Estate Agent</span>
    <div class="contact">
      <div class="address">PO Box 7316<br>Ferndale NSW 2890</div>
      <div class="contact-row">
        <svg viewBox="0 0 10 10"><path d="M2 0.5 L3.6 2.6 L2.7 3.6 Q3.8 5.8 6.3 7.2 L7.3 6.3 L9.5 7.9 L8.4 9.5 Q3.5 9 0.6 1.6 Z" fill="var(--brand-red)"/></svg>
        <span>0400 555 218</span>
      </div>
      <div class="contact-row">
        <svg viewBox="0 0 10 10"><rect x="0.6" y="2" width="8.8" height="6" fill="none" stroke="var(--brand-red)" stroke-width="1.1"/><path d="M0.8 2.3 L5 5.5 L9.2 2.3" fill="none" stroke="var(--brand-red)" stroke-width="1.1"/></svg>
        <span>liam@pimlu.com</span>
      </div>
      <div class="contact-row">
        <svg viewBox="0 0 10 10"><circle cx="5" cy="5" r="4.3" fill="none" stroke="var(--brand-red)" stroke-width="1"/><ellipse cx="5" cy="5" rx="1.8" ry="4.3" fill="none" stroke="var(--brand-red)" stroke-width="0.9"/><path d="M0.7 5 H9.3" stroke="var(--brand-red)" stroke-width="0.9"/></svg>
        <span>www.pimlu.com</span>
      </div>
    </div>
  </section>
</main>
</body>
</html>
```